Lantern Petals Website v.1 - attract floral shop franchisees

I need a simple information website for my new business. We are a franchisor of flower shops. The overall purpose of the website is to promote the company and the service, especially to potential franchisees and retailers. Only about 4 pages are required including homepage, About, For Supermarkets, For Franchisees, and Contact. No special functions are required except the site will have two separate inquiry forms that must be filled out online and submitted via automated email. Similarly, an email form should be linked from the Contact page. I have a logo and business cards designed by ArtMingle, and I would like the site to have a consistent color scheme and style. The key to design will be to express the joy and love associated with flowers and floral bouquets.
IMPORTANT - I will be exporting the website design to Wordpress CMS in a site hosted by HostNimbus. For smooth integration into WordPress hosted by HostNimbus, the designer should build the site using a WordPress-friendly format. Ideally, they should use HTML, CSS, and PHP. Creating a custom theme or using a page builder that exports to WordPress-compatible files is best. This ensures the site can be easily imported and managed within WordPress.

Target Market(s)

Potential franchisees (existing florists or creative types who might like to own a floral business) and supermarkets who might want us to run their floral department

Industry/Entity Type

Floral retailing

Requirements
Must have
• A brand theme that is beautiful, consistent throughout and builds on the logo design
Nice to have
• Show gender and ethnic diversity in customers and florists. Pictures of happy florists (for franchisees) and pictures of amazing floral department displays (for supermarkets)

```html
<!DOCTYPE html>
<html lang="en">
<head>
<meta charset="utf-8">
<title>Lantern Petals</title>
<link href="https://fonts.googleapis.com/css2?family=Poppins:wght@400;500;600;700&family=Yellowtail&display=swap" rel="stylesheet">
<style>
:root{
  --orange:#f5a10a;
  --green:#1d8a3a;
  --ink:#1f1f1f;
  --text:#333;
  --muted:#f5f5f5;
  --mint:#dcefe6;
  --footer:#0b0b0b;
  --white:#fff;
}
*{margin:0;padding:0;box-sizing:border-box}
html,body{width:1200px;height:3474px;overflow:hidden}
body{position:relative;font-family:'Poppins',sans-serif;color:var(--text);background:#fafafa}
.abs{position:absolute}
.script{font-family:'Yellowtail',cursive;font-weight:400}

/* hero */
.hero{left:0;top:0;width:1200px;height:640px;background:linear-gradient(180deg,#f3f7f8 0%,#fbf8f4 100%);border-bottom:2px solid #efe9df;overflow:hidden}
.wash-top{left:0;top:0;width:1200px;height:260px;background:radial-gradient(ellipse at 70% 0%,rgba(196,224,232,.55),transparent 60%)}
.flowers-left{left:0;top:90px;width:150px;height:170px;border-radius:50%;background:radial-gradient(circle at 45% 35%,#e23d7a 0%,#f07aa6 30%,#f6b3ca 50%,rgba(248,200,215,0) 72%)}
.flowers-right{left:1020px;top:470px;width:220px;height:200px;border-radius:50%;background:radial-gradient(circle at 55% 55%,#f06c4a 0%,#f59c80 35%,#f9c9b6 55%,rgba(252,220,205,0) 74%)}
.brand{left:141px;top:38px;display:flex;align-items:center;gap:12px}
.brand-dot{width:58px;height:58px;border-radius:50%;background:var(--orange)}
.brand-name{font-size:32px;font-weight:600;color:var(--green);line-height:1}
.nav{left:615px;top:57px;font-size:13px;color:var(--ink)}
.nav a{position:absolute;white-space:nowrap;text-decoration:none;color:var(--ink)}
.nav a.active{color:var(--orange);border-bottom:1px solid var(--orange);padding-bottom:2px}
.hero-title{left:139px;top:205px;width:500px;font-size:37px;font-weight:600;line-height:42px;color:var(--ink)}
.hero-copy{left:142px;top:343px;width:460px;font-size:12px;line-height:20px;color:#222}
.btn-pill{left:141px;top:427px;width:142px;height:35px;border-radius:18px;background:var(--orange);color:#fff;font-size:12px;display:flex;align-items:center;padding-left:16px}
.btn-pill i{position:absolute;right:4px;top:4px;width:27px;height:27px;border-radius:50%;background:#fff}
.hero-ring{left:647px;top:121px;width:458px;height:458px;border-radius:50%;background:#fff;box-shadow:0 4px 24px rgba(0,0,0,.08)}
.hero-photo{left:655px;top:129px;width:442px;height:442px;border-radius:50%;
  background:
    radial-gradient(circle at 30% 25%,#f4f2ec 0,#eae6dc 12%,transparent 24%),
    radial-gradient(circle at 72% 30%,#f1f0e6 0,#e4e6d4 12%,transparent 24%),
    radial-gradient(circle at 62% 55%,#e25a96 0,#d9468a 14%,transparent 28%),
    radial-gradient(circle at 25% 65%,#c8325e 0,#b22a52 14%,transparent 28%),
    radial-gradient(circle at 80% 75%,#e0508e 0,transparent 24%),
    radial-gradient(circle at 45% 85%,#b83068 0,transparent 24%),
    linear-gradient(160deg,#7a7c7c 0%,#3f7a3a 40%,#2f5e2c 70%,#8a6a48 100%)}

/* about */
.about{left:0;top:640px;width:1200px;height:674px;background:#fafafa;overflow:hidden}
.hex{clip-path:polygon(25% 0,75% 0,100% 50%,75% 100%,25% 100%,0 50%)}
.hex-back{background:var(--mint)}
.about-back{left:165px;top:70px;width:400px;height:370px}
.about-photo{left:141px;top:84px;width:405px;height:354px;
  background:
    radial-gradient(ellipse at 50% 30%,#9fa3a0 0,#8b8f8c 14%,transparent 26%),
    radial-gradient(circle at 30% 65%,#f07a2a 0,transparent 18%),
    radial-gradient(circle at 62% 68%,#f3d21e 0,#e9c12a 16%,transparent 28%),
    radial-gradient(ellipse at 45% 90%,#c9d8ec 0,#b4c8e0 18%,transparent 34%),
    linear-gradient(180deg,#b9c69c 0%,#a8b78c 45%,#5e6a52 100%)}
.mini-dot{width:22px;height:22px;border-radius:50%;background:var(--orange)}
.about-title{left:584px;top:126px;font-size:40px;line-height:1.1;color:var(--ink)}
.about-title .o{color:var(--orange)}.about-title .g{color:var(--green)}
.about-copy{left:586px;top:186px;width:474px;font-size:11.5px;line-height:23px;color:#2a2a2a}
.about-copy p+p{margin-top:11px}
.about-wide{left:166px;top:485px;width:880px;font-size:11.5px;line-height:23px;color:#2a2a2a}
.sprig{left:1040px;top:340px;width:150px;height:330px;border-radius:50%;background:radial-gradient(ellipse,rgba(200,228,214,.6),transparent 70%)}

/* partner */
.partner{left:0;top:1314px;width:1200px;height:551px;background:var(--muted);overflow:hidden}
.partner-wash-l{left:-60px;top:-20px;width:260px;height:320px;border-radius:50%;background:radial-gradient(ellipse,rgba(244,196,196,.45),transparent 70%)}
.partner-wash-r{left:1040px;top:380px;width:220px;height:220px;border-radius:50%;background:radial-gradient(ellipse,rgba(246,190,180,.5),transparent 70%)}
.partner-mark{left:141px;top:122px;display:flex;align-items:center;gap:10px}
.partner-mark i{width:40px;height:40px;border-radius:50%;background:#d6a24a}
.partner-mark span{font-size:14px;font-weight:600;letter-spacing:3px;color:var(--ink)}
.partner-copy{left:141px;top:234px;width:470px;font-size:11.5px;line-height:23px;color:#2a2a2a}
.partner-copy p+p{margin-top:6px}
.btn-box{height:42px;background:var(--orange);color:var(--ink);font-size:13.5px;font-weight:500;display:flex;align-items:center;justify-content:center}
.partner-btn{left:141px;top:389px;width:127px}
.partner-back{left:710px;top:85px;width:400px;height:380px}
.partner-photo{left:685px;top:101px;width:405px;height:351px;
  background:
    radial-gradient(ellipse at 55% 42%,#2a2a26 0,#3a3a34 12%,transparent 20%),
    radial-gradient(ellipse at 55% 48%,#f6f3ee 0,#ece6dc 22%,transparent 34%),
    radial-gradient(ellipse at 85% 40%,#a86a48 0,transparent 22%),
    radial-gradient(ellipse at 30% 80%,#8a5236 0,transparent 26%),
    linear-gradient(160deg,#5a5048 0%,#3a6a50 40%,#1f7a48 60%,#2a5a3c 100%)}

/* reviews */
.reviews{left:0;top:1865px;width:1200px;height:485px;background:#fafafa;overflow:hidden}
.reviews-dot{left:589px;top:64px}
.reviews-title{left:0;top:108px;width:1200px;text-align:center;font-size:40px}
.reviews-title .o{color:var(--orange)}.reviews-title .g{color:var(--green)}
.card{top:175px;width:445px;height:225px;background:#fff;box-shadow:0 3px 14px rgba(0,0,0,.08);text-align:center}
.card::after{content:"";position:absolute;left:12px;right:12px;bottom:-2px;height:3px;background:#f3d7a4;border-radius:2px}
.card .quote{font-size:110px;line-height:80px;height:60px;color:#e4e4e4;font-family:Georgia,serif;padding-top:14px}
.card .stars{display:flex;justify-content:center;gap:4px;margin-top:-6px}
.card .txt{margin:10px 18px 0;font-size:12px;line-height:22px;color:#333}
.card .name{margin-top:4px;font-size:13.5px;font-weight:500;color:var(--ink)}
.arrow{width:36px;height:36px;border-radius:50%;display:flex;align-items:center;justify-content:center}
.arrow-prev{left:83px;top:268px;background:#fff;box-shadow:0 1px 6px rgba(0,0,0,.15)}
.arrow-next{left:1079px;top:268px;background:var(--green)}

/* gallery */
.gallery{left:0;top:2350px;width:1200px;height:791px;background:#fafafa}
.tile{position:absolute}
.gallery-btn{left:537px;top:664px;width:126px}

/* footer */
.footer{left:0;top:3141px;width:1200px;height:290px;background:var(--footer);color:#fff}
.f-head{font-size:22px;color:var(--orange)}
.f-links{list-style:none;font-size:12px}
.f-links li{height:33px}
.f-contact{display:flex;align-items:center;gap:14px;font-size:12px;line-height:18px;position:absolute}
.f-icon{width:40px;height:40px;border-radius:50%;background:#2a2a2a;display:flex;align-items:center;justify-content:center}
.f-brand{left:858px;top:70px;display:flex;align-items:center;gap:10px}
.f-brand i{width:46px;height:46px;border-radius:50%;background:var(--orange)}
.f-brand span{font-size:26px;font-weight:600;color:var(--orange)}
.social{top:185px;width:36px;height:36px;border-radius:50%;background:#2c2c2c;border:1px solid #555}
.bottom-bar{left:0;top:3431px;width:1200px;height:43px;background:var(--orange);font-size:13px;color:#222;display:flex;align-items:center;justify-content:center}
</style>
</head>
<body>

<section class="hero abs">
  <div class="wash-top abs"></div>
  <div class="flowers-left abs" role="img" aria-label="Watercolour pink flowers"></div>
  <div class="flowers-right abs" role="img" aria-label="Watercolour peach flowers"></div>
  <div class="brand abs"><i class="brand-dot"></i><span class="brand-name">Lantern Petals</span></div>
  <nav class="nav abs">
    <a class="active" style="left:0;top:0">About Us</a>
    <a style="left:95px;top:0">For Supermakets</a>
    <a style="left:241px;top:0">For Franchisees</a>
    <a style="left:378px;top:0">Contact Us</a>
  </nav>
  <h1 class="hero-title abs">Flowers Expressed Feelings Of Surprise, Happiness and gratitude.</h1>
  <p class="hero-copy abs">Get franchisor of flower shops. Nibh euismod tincidunt ut laoreet dolore magna aliquam erat volutpat. Ut wisi enim ad minim veniam.</p>
  <div class="btn-pill abs">Get Franchisee<i></i></div>
  <div class="hero-ring abs"></div>
  <div class="hero-photo abs" role="img" aria-label="Photo of a bouquet of pink roses and white hydrangeas"></div>
</section>

<section class="about abs">
  <div class="sprig abs" role="img" aria-label="Faint watercolour leaves"></div>
  <div class="about-back abs hex hex-back"></div>
  <div class="about-photo abs hex" role="img" aria-label="Photo of a florist holding bright bouquets"></div>
  <i class="mini-dot abs" style="left:587px;top:90px"></i>
  <h2 class="about-title abs script">About <span class="o">Lantern</span> <span class="g">Petals</span></h2>
  <div class="about-copy abs">
    <p>Fresh flowers convey beauty and love, &amp; in our view should become something every person regularly enjoys. Lantern Petals is an entrepreneurial company created to make top quality fresh flowers &amp; professionally-designed bouquets accessible to every consumer at affordable prices.</p>
    <p>Professional florists typically sell the finest quality stems, design the most beautiful bouquets and provide the finest customer service, but their costs – of floral products, retail spaces, labor and marketing – force them to pass high prices along to customers. Supermarket flower departments benefit from high customer footfall, economies of scale and low pricing, but their quality of stems and bouquets is typically poor, staffing is limited, and staff turnover is high which can result in inefficiency, wastage, poorly merchandised selections and limited service.</p>
  </div>
  <p class="about-wide abs">Lantern Petals brings the best of professional florists and supermarkets together for the benefit of consumers. It supports a national network of owner-operator franchisees, who in many cases are multi-site professional florists, with comprehensive services to enhance franchise profitability. Lantern Petals works with some of the country's largest and most progressive supermarkets to provide franchisee ownership and operation of their strategically important floral departments. Supermarkets find that Lantern Petals is able to improve their financial outcomes, provide attentive customer service and satisfaction, and lift the quality of the entire store environment</p>
</section>

<section class="partner abs">
  <div class="partner-wash-l abs" role="img" aria-label="Faint watercolour flowers"></div>
  <div class="partner-wash-r abs" role="img" aria-label="Faint watercolour flowers"></div>
  <div class="partner-mark abs"><i></i><span>FROSTWREN GROUP</span></div>
  <div class="partner-copy abs">
    <p>Lantern Petals operates in partnership with Frostwren Group, the leading franchisor of sushi stations and pre-packaged fruit &amp; vegetable departments to supermarkets across the United States and United Kingdom.</p>
    <p>Lantern Petals' combination of floral and supermarket franchising expertise guarantees that consumers, franchisees and supermarket partners each receive exceptional service and value.</p>
  </div>
  <div class="btn-box partner-btn abs">Contact Us</div>
  <div class="partner-back abs hex hex-back"></div>
  <div class="partner-photo abs hex" role="img" aria-label="Photo of hands passing a plate of sushi rolls"></div>
</section>

<section class="reviews abs">
  <i class="mini-dot abs reviews-dot"></i>
  <h2 class="reviews-title abs script"><span class="o">Customer</span> <span class="g">Reviews</span></h2>
  <div class="arrow arrow-prev abs"><svg width="12" height="12" viewBox="0 0 12 12"><path d="M8 2 4 6l4 4" fill="none" stroke="#1d8a3a" stroke-width="1.8"/></svg></div>
  <article class="card abs" style="left:140px">
    <div class="quote">&ldquo;</div>
    <div class="stars">
      <svg width="64" height="13" viewBox="0 0 80 16" fill="#f5a10a"><g id="st"><path d="M8 0l2.4 5 5.6.8-4 3.9.9 5.5L8 12.6 3.1 15.2l.9-5.5-4-3.9 5.6-.8z"/></g><use href="#st" x="16"/><use href="#st" x="32"/><use href="#st" x="48"/><use href="#st" x="64"/></svg>
    </div>
    <p class="txt">Suspendisse ornare non turpis pellentesque sollicitudin. Vestibulum non tellus porttitor leo porttitor posuere. Cras ac egestas enim, a pretium elit. Curabitur euismod velit nibh, eget ultricies orci vulputate in. In placerat eroseget erat dictum...</p>
    <p class="name">Marcus Hale</p>
  </article>
  <article class="card abs" style="left:613px">
    <div class="quote">&ldquo;</div>
    <div class="stars">
      <svg width="64" height="13" viewBox="0 0 80 16" fill="#f5a10a"><use href="#st"/><use href="#st" x="16"/><use href="#st" x="32"/><use href="#st" x="48"/><use href="#st" x="64"/></svg>
    </div>
    <p class="txt">Suspendisse ornare non turpis pellentesque sollicitudin. Vestibulum non tellus porttitor leo porttitor posuere. Cras ac egestas enim, a pretium elit. Curabitur euismod velit nibh, eget ultricies orci vulputate in. In placerat eroseget erat dictum...</p>
    <p class="name">Marcus Hale</p>
  </article>
  <div class="arrow arrow-next abs"><svg width="12" height="12" viewBox="0 0 12 12"><path d="M4 2l4 4-4 4" fill="none" stroke="#fff" stroke-width="1.8"/></svg></div>
</section>

<section class="gallery abs">
  <div class="tile" style="left:141px;top:84px;width:451px;height:269px;background:radial-gradient(ellipse at 55% 40%,#c9302e 0,#d84a3e 8%,transparent 18%),radial-gradient(ellipse at 30% 35%,#a87a48 0,transparent 16%),radial-gradient(ellipse at 50% 90%,#f2d13a 0,#9ab85a 22%,transparent 45%),linear-gradient(180deg,#eeebe6 0%,#e0dbd2 55%,#6f9a4c 100%)" role="img" aria-label="Photo of a smiling florist in her flower shop"></div>
  <div class="tile" style="left:607px;top:84px;width:218px;height:269px;background:radial-gradient(circle at 35% 45%,#d8572a 0,transparent 20%),radial-gradient(circle at 65% 55%,#f2b21e 0,#e69a1e 14%,transparent 28%),radial-gradient(circle at 50% 20%,#7a8a3a 0,transparent 30%),linear-gradient(180deg,#4a5a30 0%,#5a6a3a 50%,#2e2e2a 100%)" role="img" aria-label="Photo of a bouquet with orange proteas"></div>
  <div class="tile" style="left:840px;top:84px;width:218px;height:269px;background:radial-gradient(ellipse at 58% 55%,#cfcbc2 0,#b8b2a6 18%,transparent 32%),radial-gradient(circle at 25% 40%,#c8506a 0,transparent 18%),radial-gradient(ellipse at 85% 30%,#7a8a82 0,transparent 25%),linear-gradient(180deg,#5a3d2c 0%,#6a4a34 55%,#3a2a20 100%)" role="img" aria-label="Photo of a florist arranging flowers at a counter"></div>
  <div class="tile" style="left:141px;top:368px;width:219px;height:267px;background:radial-gradient(circle at 30% 35%,#f2f0e8 0,transparent 20%),radial-gradient(circle at 70% 40%,#eef0e0 0,transparent 20%),radial-gradient(circle at 75% 75%,#dc4c8a 0,transparent 24%),radial-gradient(circle at 25% 75%,#b82a50 0,transparent 22%),linear-gradient(180deg,#8a8a8a 0%,#3f7a3a 45%,#2f5e2c 85%,#8a6a48 100%)" role="img" aria-label="Photo of roses and hydrangeas on a table"></div>
  <div class="tile" style="left:375px;top:368px;width:218px;height:267px;background:radial-gradient(ellipse at 40% 30%,#d9b8a0 0,transparent 18%),radial-gradient(ellipse at 35% 65%,#2e3a58 0,transparent 28%),radial-gradient(circle at 75% 70%,#d02a3a 0,#e85a6a 16%,transparent 30%),radial-gradient(circle at 80% 30%,#6a8a9a 0,transparent 26%),linear-gradient(180deg,#ece8e2 0%,#d6d2ca 45%,#4a7a3a 100%)" role="img" aria-label="Photo of a florist arranging red and pink flowers"></div>
  <div class="tile" style="left:607px;top:368px;width:451px;height:267px;background:radial-gradient(ellipse at 50% 55%,#6a3a2a 0,#8a5a3a 10%,transparent 22%),radial-gradient(ellipse at 22% 45%,#e2a8c0 0,transparent 26%),radial-gradient(ellipse at 78% 45%,#e6aec4 0,transparent 26%),radial-gradient(ellipse at 50% 90%,#c8a0b0 0,#5a7a4a 30%,transparent 55%),linear-gradient(180deg,#3a463c 0%,#4a5a48 25%,#a69a8a 100%)" role="img" aria-label="Photo of a flower shop front full of pink blooms"></div>
  <div class="btn-box gallery-btn abs">Contact Us</div>
</section>

<footer class="footer abs">
  <h3 class="f-head script abs" style="left:141px;top:50px">Quick Links</h3>
  <ul class="f-links abs" style="left:141px;top:89px">
    <li>• Home</li><li>• About Us</li><li>• For Supermarkets</li><li>• For Franchisees</li><li>• Contact Us</li>
  </ul>
  <h3 class="f-head script abs" style="left:453px;top:50px">Contact Details</h3>
  <div class="f-contact" style="left:453px;top:92px">
    <span class="f-icon"><svg width="14" height="18" viewBox="0 0 14 18"><path d="M7 0a7 7 0 0 0-7 7c0 5 7 11 7 11s7-6 7-11a7 7 0 0 0-7-7zm0 9.5A2.5 2.5 0 1 1 7 4.5a2.5 2.5 0 0 1 0 5z" fill="#f5a10a"/></svg></span>
    <span>48 Fernbrook Lane, Suite 5<br>Maple Grove, ST 20481</span>
  </div>
  <div class="f-contact" style="left:453px;top:143px">
    <span class="f-icon"><svg width="16" height="16" viewBox="0 0 16 16"><path d="M3.6 1.2 6 3.6 4.6 5.6c.9 2 2.8 3.9 4.8 4.8l2-1.4 2.4 2.4-1.8 2.4C6.8 13.4 2.6 9.2 1.2 3z" fill="#f5a10a"/></svg></span>
    <span>555-204-3186</span>
  </div>
  <div class="f-contact" style="left:453px;top:194px">
    <span class="f-icon"><svg width="16" height="12" viewBox="0 0 16 12"><rect width="16" height="12" rx="1.5" fill="#f5a10a"/><path d="M1 1.5 8 7l7-5.5" fill="none" stroke="#2a2a2a" stroke-width="1.3"/></svg></span>
    <span>info@lanternpetals.com</span>
  </div>
  <div class="f-brand abs"><i></i><span>Lantern Petals</span></div>
  <span class="social abs" style="left:873px"></span>
  <span class="social abs" style="left:916px"></span>
  <span class="social abs" style="left:961px"></span>
  <span class="social abs" style="left:1004px"></span>
</footer>
<div class="bottom-bar abs">©2024 Lantern Petals. All Rights Reserved.</div>

</body>
</html>
```